Web Design Project

We need a web design company for a company based in London. We are an online minicab booking service that produces real time quotes on cab journey for consumers. Our colours are currently red and yellow, but do not need to stay that way; it's open to interpretation. Please avoid yellow and black as a colour combination. Our current site is: www.rovelink.co.uk We are looking for a new site to be user-friendly and easy to use, but more polished and professional looking, without using it usability and simplicity. We need to keep the booking capability on each page and it needs to draw in the user's eye. We need a site that is reliable and easy to use, but also fun.

Main objective: keep it simple, like it is now, but polish it up some. Also, we need to be able to add more content to it. And, we will also be adding a login capability for return users.

Target Market(s)

Internet-savvy people aged 18 and older.

Industry/Entity Type

It Company

Requirements
Must have
• Must have the booking widget. However, it doesn't have to be as large as it is now. We are actually thinking to split it over two pages. We will add a few options to the booking widget, such as another via option. The booking widget must be the most noticeable feature on the page. Sans serif font, please.
Should not have
• Should not be too busy and distracting. Please do not use any images of traditional taxis, ie. black cabs from London or yellow cabs from NYC. Our cars do not resemble these and our business cannot be associated with these images.

```html
<!DOCTYPE html>
<html lang="en">
<head>
<meta charset="utf-8">
<title>Rovelink – Minicab booking</title>
<link rel="stylesheet" href="https://fonts.googleapis.com/css2?family=Arimo:wght@400;700&family=Oswald:wght@400&family=Ubuntu:wght@400;500;700&family=Kalam:wght@700&display=swap">
<style>
:root{
  --header-top:#4a4a4a;
  --header-bottom:#1e1e1e;
  --orange-light:#f0a032;
  --orange:#e58a1f;
  --orange-deep:#c8650c;
  --page:#efefef;
  --panel:#f4f4f4;
  --panel-edge:#c9c9c9;
  --text:#3a3a3a;
  --heading:#2a2a2a;
  --muted:#777;
  --blue:#2d5a8f;
  --link:#3d7fc4;
  --white:#ffffff;
  --dark-btn:#2e2e2e;
  --footer-top:#333;
  --footer-bottom:#4a4a4a;
  --line:#bdbdbd;
}
*{box-sizing:border-box;margin:0;padding:0}
html,body{width:956px;height:1200px;overflow:hidden}
body{position:relative;background:var(--page);font-family:Arimo,Arial,sans-serif;color:var(--text)}
.abs{position:absolute}

/* header */
.site-header{position:absolute;left:0;top:0;width:956px;height:88px;background:linear-gradient(var(--header-top),var(--header-bottom))}
.brand{position:absolute;left:108px;top:22px;font:700 34px Arimo,Arial,sans-serif;color:var(--orange)}
.main-nav{position:absolute;left:350px;top:0;height:88px;display:flex}
.main-nav a{display:flex;align-items:center;height:88px;padding:0 16px;color:var(--white);font-size:14px;text-decoration:none;border-left:1px solid #222;border-right:1px solid #555}
.main-nav a.current{background:repeating-linear-gradient(45deg,#3a3a3a 0 2px,#333 2px 4px)}
.account{position:absolute;left:775px;top:40px;font-size:12px;color:var(--white)}
.account a{color:var(--orange);text-decoration:underline}

/* hero */
.hero{position:absolute;left:0;top:88px;width:956px;height:304px;background:linear-gradient(var(--orange-light),var(--orange) 55%,var(--orange-deep))}
.step{position:absolute;color:var(--white)}
.step-title{font:700 36px Kalam,cursive;line-height:1}
.step-text{font-size:14px;line-height:20px;margin-top:20px}
.route-search{position:absolute;left:132px;top:330px;display:flex;height:27px}
.route-search input{width:175px;border:0;padding:0 13px;font:italic 10px Arimo,Arial,sans-serif;color:#888}
.route-search button{width:50px;border:0;background:var(--dark-btn);color:var(--white);font:700 12px Arimo,Arial,sans-serif}
.cab-illustration{position:absolute;left:757px;top:176px;width:120px;height:106px;border-radius:16px;background:#1f1f1f}

/* content */
h2{font:400 24px Oswald,sans-serif;color:var(--heading)}
.copy{font-size:11.5px;line-height:21px}
.copy p+p{margin-top:5px}
.why h3{font:700 13px Arimo,Arial,sans-serif;color:var(--heading);margin:14px 0 6px}
.learn-more{position:absolute;left:164px;top:700px;font:italic 12px Arimo,Arial,sans-serif;color:var(--link);display:flex;align-items:center;gap:14px}
.divider{position:absolute;left:71px;top:808px;width:470px;height:1px;background:var(--line)}
.stories h2{font:700 18px Arimo,Arial,sans-serif}
.stories .copy{font-size:11.5px;line-height:20px;margin-top:10px}
.send{position:absolute;left:416px;top:1058px;font-size:15px;color:#555}
.send a{color:var(--link)}

/* booking */
.booking{position:absolute;left:611px;top:431px;width:278px;height:652px;background:var(--panel);border:1px solid var(--panel-edge);border-radius:8px;box-shadow:0 2px 6px rgba(0,0,0,.2)}
.booking-title{height:40px;border-bottom:1px solid #ccc;text-align:center;font:700 25px Ubuntu,sans-serif;color:var(--blue);line-height:40px}
.field-label{position:absolute;left:24px;font-size:12px;color:#333}
.field{position:absolute;left:24px;height:26px;background:var(--white);border:1px solid #c8c8c8;border-radius:3px;font:italic 10px Arimo,Arial,sans-serif;color:#888;padding:0 10px;display:flex;align-items:center}
.find{position:absolute;width:53px;height:26px;background:var(--dark-btn);color:var(--white);font:700 12px Arimo,Arial,sans-serif;display:flex;align-items:center;justify-content:center;border-radius:0 3px 3px 0}
.select{position:absolute;height:18px;background:var(--white);border:1px solid #aaa}
.select::after{content:"";position:absolute;right:0;top:0;width:14px;height:16px;border-left:1px solid #aaa;background:linear-gradient(#fff,#ddd)}
.select i{position:absolute;right:4px;top:7px;border:3px solid transparent;border-top:4px solid #222;z-index:1}
.small-label{position:absolute;font-size:10px;color:#333}
.check{position:absolute;width:16px;height:16px;border:1px solid #bbb;background:var(--white)}
.quote-btn{position:absolute;left:29px;top:592px;width:220px;height:31px;border-radius:5px;background:linear-gradient(#f19a2c,#d86f10);box-shadow:0 0 0 3px #e6e6e6;color:var(--white);font:500 14px Ubuntu,sans-serif;display:flex;align-items:center;justify-content:center}

/* footer */
.site-footer{position:absolute;left:0;top:1113px;width:956px;height:87px;background:linear-gradient(90deg,var(--footer-top),var(--footer-bottom) 50%,var(--footer-top))}
.legal{position:absolute;left:71px;top:27px;font-size:10px;line-height:16px;color:var(--white)}
.legal a{color:var(--orange)}
.legal .policy{color:var(--white)}
.follow{position:absolute;left:715px;top:33px;font-size:10px;color:var(--white)}
.social{position:absolute;top:20px;width:27px;height:27px;border-radius:50%;background:linear-gradient(#eee,#b5b5b5)}
</style>
</head>
<body>

<header class="site-header">
  <div class="brand">Rovelink</div>
  <nav class="main-nav">
    <a class="current" href="#">Rovelink Miles</a>
    <a href="#">Join Us</a>
    <a href="#">About Us</a>
    <a href="#">Contact Us</a>
  </nav>
  <div class="account"><a href="#">login</a> &nbsp; or &nbsp; <a href="#">sign up</a></div>
</header>

<section class="hero">
  <svg class="abs" style="left:0;top:0" width="956" height="304" viewBox="0 88 956 304" fill="none" stroke="#fff" stroke-width="2" stroke-linecap="round">
    <!-- step icons -->
    <rect x="136" y="130" width="28" height="34" fill="#fff" stroke="none"/>
    <g stroke="#e58a1f" stroke-width="2"><line x1="141" y1="138" x2="159" y2="138"/><line x1="141" y1="144" x2="159" y2="144"/><line x1="141" y1="150" x2="159" y2="150"/><line x1="151" y1="156" x2="159" y2="156"/></g>
    <line x1="370" y1="128" x2="370" y2="162"/><line x1="354" y1="136" x2="386" y2="136"/>
    <path d="M354 136 l-6 12 h12 z M386 136 l-6 12 h12 z"/><line x1="360" y1="162" x2="380" y2="162"/>
    <rect x="582" y="136" width="40" height="26" fill="#fff" stroke="none"/>
    <path d="M582 136 l20 16 l20 -16" stroke="#e58a1f"/>
    <!-- connecting curves -->
    <path d="M104 258 C88 290 92 330 126 343"/><path d="M118 336 l9 7 l-10 4"/>
    <path d="M362 345 C420 335 440 300 436 262"/><path d="M430 270 l6 -9 l4 10"/>
    <path d="M428 180 C470 150 510 150 545 168"/><path d="M536 162 l10 6 l-10 5"/>
    <path d="M635 288 C660 330 720 330 770 296"/><path d="M760 296 l11 0 l-4 10"/>
  </svg>

  <div class="step" style="left:87px;top:92px"><div class="step-title">Step 1</div><div class="step-text">Enter your route</div></div>
  <div class="step" style="left:313px;top:92px"><div class="step-title">Step 2</div><div class="step-text">Quickly compare taxi fares</div></div>
  <div class="step" style="left:539px;top:92px"><div class="step-title">Step 3</div><div class="step-text">Get your travel confirmed<br>on your phone by SMS.</div></div>

  <form class="route-search" style="top:242px"><input value="Old street" aria-label="Route"><button type="button">Find</button></form>
  <div class="cab-illustration" style="top:88px" role="img" aria-label="Illustration of a cab seen from the front"></div>
</section>

<section class="who abs" style="left:71px;top:440px;width:220px">
  <h2>Who we are?</h2>
  <div class="copy" style="margin-top:18px">
    <p>At Rovelink, we offer a service which allows you to book the quickest and cheapest minicab wherever you are in London.</p>
    <p>With Rovelink.co.uk you will receive instant price comparisons of fares and pickup times of any cab you may need, before booking the right car for you.</p>
  </div>
</section>
<a class="learn-more" href="#">Learn more
  <svg width="22" height="22" viewBox="0 0 22 22" fill="none" stroke="#3d7fc4" stroke-width="2"><circle cx="11" cy="11" r="9.5"/><path d="M6 11h9M11 7l4 4-4 4"/></svg>
</a>

<section class="why abs" style="left:332px;top:440px;width:210px">
  <h2>Why Rovelink?</h2>
  <h3>Price</h3>
  <p class="copy">Rovelink guarantees that you get the best deal for your travel, as you get quotes from several cab companies.</p>
  <h3>No fees</h3>
  <p class="copy">There's absolutely no cost for you to use our service.</p>
  <h3>Coverage</h3>
  <p class="copy">Rovelink has the largest database of licensed minicab operators. You can use Rovelink wherever you are in greater London.</p>
</section>

<div class="divider"></div>

<section class="stories abs" style="left:71px;top:840px;width:475px">
  <h2>The best stories from our community</h2>
  <p class="copy">I recently hit London for a girlie night on the town with my bestie. After a little too much champagne, we had a stupid argument and decided to leave the club early. In the cab on our way home, we didn't say one word to each other. The driver who could sense we were both upset however, had other plans. He randomly started singing The Marlows' Midnight Waltz! My best friend and I were in shock, we looked at each other and couldn't stop laughing! The remainder of the journey consisted of us all belting out Marlows classics, in between fits of laughter. We were so disappointed when we arrived home as we wanted to continue the fun, we will never forget our singing taxi driver!</p>
</section>
<p class="send"><a href="#">Send</a> us your story!</p>

<aside class="booking">
  <div class="booking-title">book a cab</div>
  <span class="field-label" style="top:56px">Pick me up from:</span>
  <div class="field" style="top:75px;width:174px">e.g.&nbsp; pick up address or post code</div>
  <div class="find" style="left:197px;top:75px">Find</div>
  <span class="field-label" style="top:115px">Drop me at:</span>
  <div class="field" style="top:133px;width:174px">e.g.&nbsp; drop address or post code</div>
  <div class="find" style="left:197px;top:133px">Find</div>
  <span class="field-label" style="top:170px">Pick up date and time:</span>
  <div class="field" style="top:188px;width:175px;font-style:normal">5 Apr 2012 @ 12:02</div>
  <svg class="abs" style="left:215px;top:187px" width="36" height="30" viewBox="0 0 36 30">
    <rect x="1" y="4" width="34" height="25" fill="#fff" stroke="#bbb"/><rect x="1" y="4" width="34" height="6" fill="#3d6fb0"/>
    <g fill="#ccc"><rect x="5" y="14" width="5" height="4"/><rect x="12" y="14" width="5" height="4"/><rect x="19" y="14" width="5" height="4"/><rect x="26" y="14" width="5" height="4"/><rect x="5" y="21" width="5" height="4"/><rect x="12" y="21" width="5" height="4"/><rect x="19" y="21" width="5" height="4"/></g>
  </svg>
  <span class="small-label" style="left:24px;top:232px">Just pick me up in</span>
  <div class="select" style="left:121px;top:229px;width:78px"><i></i></div>
  <span class="small-label" style="left:24px;top:260px">Passenger:</span>
  <div class="select" style="left:86px;top:256px;width:43px"><i></i></div>
  <span class="small-label" style="left:147px;top:260px">Luggage:</span>
  <div class="select" style="left:198px;top:256px;width:53px"><i></i></div>
  <div class="check" style="left:24px;top:290px"></div>
  <svg class="abs" style="left:24px;top:285px" width="20" height="20" viewBox="0 0 20 20"><path d="M4 11l4 5 9-13" fill="none" stroke="#3d6fb0" stroke-width="2"/></svg>
  <span class="field-label" style="left:50px;top:292px">Return Journey</span>
  <div class="check" style="left:149px;top:290px"></div>
  <span class="field-label" style="left:175px;top:292px">Extras</span>
  <span class="field-label" style="top:324px">Mobile Number:</span>
  <div class="field" style="top:339px;width:227px"></div>
  <span class="field-label" style="top:381px">Name:</span>
  <div class="field" style="top:395px;width:227px"></div>
  <span class="field-label" style="top:438px">Email:</span>
  <div class="field" style="top:452px;width:227px"></div>
  <span class="field-label" style="top:495px">Comments:</span>
  <div class="field" style="top:508px;width:227px;height:61px"></div>
  <div class="quote-btn">Get your no obligation quotes</div>
</aside>

<footer class="site-footer">
  <div class="legal">© <a href="#">Rovelink</a> 2011-2012<br><a class="policy" href="#">Privacy Policy</a></div>
  <span class="follow">Follow Us on:</span>
  <span class="social" style="left:786px"></span>
  <span class="social" style="left:820px"></span>
  <span class="social" style="left:854px"></span>
</footer>

</body>
</html>
```